Brovick Engineering Core Values Branding Package

Brovick Engineering has recently refined its company Core Values and is seeking a strong, cohesive branding package to visually bring these values to life. The new graphic assets will communicate our commitment to excellence in a way that resonates with our team, clients, and partners in a blue-collar, industrial environment.

We are looking for multiple visual assets with consistent design elements that can be applied across platforms. The tone should reflect strength, reliability, and professionalism while remaining approachable and aligned with our industry.

Core Values & Descriptions
Accountability
“We take ownership of our work and actions, ensuring reliability and trust in every solution we deliver.”

Teamwork
“We collaborate across departments and disciplines to provide the highest level of service and innovation for our clients.”

Integrity
“We operate with honesty, transparency, and ethical standards in all aspects of our business.”

Growth
“We are committed to continuous improvement—of our people, our processes, and our impact in the industry.”

Deliverables

1. Primary Core Values Graphic
A master visual representing all four values together.
Designed for use on posters, office signage, internal presentations.

2. Individual Value Graphics (x4)
One graphic per core value: Accountability, Teamwork, Integrity, Growth.
Cohesive style with slight visual variation to reflect each value’s unique meaning.

Target Market(s)

Employees of Brovick Engineering

Industry/Entity Type

Blue Collar

Font styles to use
Sans Serif

Colors
0054AA
0677BA
7BADD7
CADEEF
E8F1F8
00AB8E
00BBA5
67D7C9
C6EFE9
E9F9F6
EB3D1F
EC4F4E
F09395
F8D3D4
FCEDEE

Requirements
Must have
• Accountability, Teamwork, Integrity, Growth

```html
<!DOCTYPE html>
<html lang="en">
<head>
<meta charset="utf-8">
<title>Brovick Engineering – Core Values Poster</title>
<link href="https://fonts.googleapis.com/css2?family=Roboto+Condensed:wght@300;400;700;800&display=swap" rel="stylesheet">
<style>
  :root{
    --canvas:#e6e7e8;
    --paper:#ffffff;
    --navy:#0f2a5c;
    --green:#34a845;
    --red:#d91f37;
    --orange:#ee7a2f;
    --mist-green:#e7f5ea;
    --mist-grey:#e3e6ec;
    --ring-grey:#b8bbc1;
  }
  html,body{margin:0;padding:0;width:1200px;height:1200px;overflow:hidden;background:var(--canvas);}
  .poster{position:absolute;left:165px;top:28px;width:870px;height:1144px;background:var(--paper);box-shadow:0 4px 14px rgba(0,0,0,.18);}
  .poster svg{display:block;width:100%;height:100%;}
  .cond{font-family:"Roboto Condensed",Arial,sans-serif;}
  .brand-name{font-weight:800;fill:var(--navy);}
  .headline{font-weight:800;fill:var(--navy);letter-spacing:1px;}
  .value-title{font-weight:700;fill:#fff;}
  .value-body{font-weight:300;fill:#fff;}
  .hub-line{font-weight:700;}
  .tagline{font-weight:400;fill:var(--green);}
</style>
</head>
<body>
<div class="poster">
<svg viewBox="0 0 1220 1605" xmlns="http://www.w3.org/2000/svg" class="cond">
  <defs>
    <linearGradient id="seg-navy" x1="0" y1="0" x2="1" y2="1"><stop offset="0" stop-color="#142c5f"/><stop offset="1" stop-color="#2b4b82"/></linearGradient>
    <linearGradient id="seg-green" x1="0" y1="0" x2="1" y2="1"><stop offset="0" stop-color="#2a9f41"/><stop offset="1" stop-color="#4cb85c"/></linearGradient>
    <linearGradient id="seg-orange" x1="0" y1="0" x2="1" y2="0"><stop offset="0" stop-color="#f7a53a"/><stop offset="1" stop-color="#e8412d"/></linearGradient>
    <linearGradient id="seg-red" x1="0" y1="0" x2="0" y2="1"><stop offset="0" stop-color="#e44257"/><stop offset="1" stop-color="#d71a32"/></linearGradient>
    <linearGradient id="hub-fill" x1="0" y1="0" x2="0" y2="1"><stop offset="0" stop-color="#9aa3b5"/><stop offset=".35" stop-color="#ffffff"/><stop offset="1" stop-color="#ffffff"/></linearGradient>
    <linearGradient id="hub-ring" x1="0" y1="0" x2="1" y2="1"><stop offset="0" stop-color="#1b3f7a"/><stop offset=".5" stop-color="#4cb85c"/><stop offset="1" stop-color="#f29a3a"/></linearGradient>
    <linearGradient id="arc-orange" x1="1" y1="0" x2="0" y2="0"><stop offset="0" stop-color="#e8412d"/><stop offset="1" stop-color="#f7a53a"/></linearGradient>
    <linearGradient id="arc-red" x1="0" y1="0" x2="0" y2="1"><stop offset="0" stop-color="#e44257"/><stop offset=".8" stop-color="#d71a32"/><stop offset="1" stop-color="#f2a23a"/></linearGradient>
  </defs>

  <!-- background bands -->
  <path class="band-green" d="M0 30 Q500 -40 930 120 Q1190 230 1220 740 L1190 740 Q1150 320 880 220 Q560 100 0 380 Z" fill="var(--mist-green)"/>
  <path class="band-grey" d="M0 640 Q420 300 820 335 Q1120 370 1135 740 L1130 740 Q1080 430 800 410 Q420 390 0 800 Z" fill="var(--mist-grey)"/>

  <!-- brand name -->
  <g class="brand">
    <circle cx="326" cy="183" r="16" fill="var(--green)"/>
    <text class="brand-name" x="628" y="206" font-size="66" text-anchor="middle">Brovick Engineering</text>
  </g>

  <text class="headline" x="610" y="465" font-size="134" text-anchor="middle">CORE VALUES</text>

  <!-- values wheel -->
  <g class="values-wheel">
    <path d="M267.9 745.5 A395 395 0 0 1 863.9 640.4" fill="none" stroke="var(--navy)" stroke-width="8"/>
    <path d="M863.9 640.4 A395 395 0 0 1 933.6 1169.6" fill="none" stroke="var(--green)" stroke-width="8"/>
    <path d="M933.6 1169.6 A395 395 0 0 1 356.1 1245.6" fill="none" stroke="url(#arc-orange)" stroke-width="8"/>
    <path d="M356.1 1245.6 A395 395 0 0 1 267.9 745.5" fill="none" stroke="url(#arc-red)" stroke-width="8"/>

    <circle cx="610" cy="943" r="362" fill="none" stroke="var(--ring-grey)" stroke-width="24"/>

    <path class="seg-accountability" d="M610 943 L369.6 702.6 A340 340 0 0 1 850.4 702.6 Z" fill="url(#seg-navy)"/>
    <path class="seg-teamwork" d="M610 943 L850.4 702.6 A340 340 0 0 1 850.4 1183.4 Z" fill="url(#seg-green)"/>
    <path class="seg-integrity" d="M610 943 L850.4 1183.4 A340 340 0 0 1 369.6 1183.4 Z" fill="url(#seg-orange)"/>
    <path class="seg-growth" d="M610 943 L369.6 1183.4 A340 340 0 0 1 369.6 702.6 Z" fill="url(#seg-red)"/>

    <circle cx="610" cy="943" r="138" fill="url(#hub-fill)" stroke="url(#hub-ring)" stroke-width="10"/>
    <text class="hub-line" x="610" y="913" font-size="32" text-anchor="middle" fill="var(--navy)">The Right People</text>
    <text class="hub-line" x="610" y="953" font-size="32" text-anchor="middle" fill="var(--green)">The Right Solutions</text>
    <text class="hub-line" x="610" y="993" font-size="32" text-anchor="middle" fill="var(--red)">Right Now!</text>

    <g class="value value-accountability" text-anchor="middle">
      <text class="value-title" x="579" y="675" font-size="32">ACCOUNTABILITY</text>
      <text class="value-body" x="579" y="708" font-size="19">We take ownership of our</text>
      <text class="value-body" x="579" y="730" font-size="19">work and actions, ensuring</text>
      <text class="value-body" x="579" y="752" font-size="19">reliability and trust in every</text>
      <text class="value-body" x="579" y="774" font-size="19">solution we deliver.</text>
      <rect x="722" y="695" width="62" height="66" rx="8" fill="#ffffff" opacity=".18" role="img" aria-label="Icon: hand holding a report with bar chart"/>
    </g>

    <g class="value value-teamwork" text-anchor="middle">
      <text class="value-title" x="862" y="871" font-size="32">TEAMWORK</text>
      <text class="value-body" x="862" y="904" font-size="18">We collaborate across</text>
      <text class="value-body" x="862" y="925" font-size="18">departments and</text>
      <text class="value-body" x="862" y="946" font-size="18">disciplines to provide the</text>
      <text class="value-body" x="862" y="967" font-size="18">highest level of service</text>
      <text class="value-body" x="862" y="988" font-size="18">and innovation for our</text>
      <text class="value-body" x="862" y="1009" font-size="18">clients.</text>
      <rect x="790" y="1045" width="70" height="70" rx="35" fill="#ffffff" opacity=".18" role="img" aria-label="Icon: three people around a gear"/>
    </g>

    <g class="value value-integrity" text-anchor="middle">
      <text class="value-title" x="617" y="1148" font-size="32">INTEGRITY</text>
      <text class="value-body" x="617" y="1181" font-size="19">We operate with honesty,</text>
      <text class="value-body" x="617" y="1203" font-size="19">transparency, and ethical</text>
      <text class="value-body" x="617" y="1225" font-size="19">standards in all aspects of</text>
      <text class="value-body" x="617" y="1247" font-size="19">our business.</text>
      <rect x="422" y="1110" width="64" height="70" rx="8" fill="#ffffff" opacity=".2" role="img" aria-label="Icon: hands holding a shield with a tick"/>
    </g>

    <g class="value value-growth" text-anchor="middle">
      <text class="value-title" x="362" y="891" font-size="32">GROWTH</text>
      <text class="value-body" x="362" y="924" font-size="18">We are committed to</text>
      <text class="value-body" x="362" y="945" font-size="18">continuous improvement</text>
      <text class="value-body" x="362" y="966" font-size="18">of our people, our</text>
      <text class="value-body" x="362" y="987" font-size="18">processes, and our</text>
      <text class="value-body" x="362" y="1008" font-size="18">impact in the industry.</text>
      <g class="icon-growth" fill="none" stroke="#fff" stroke-width="3">
        <line x1="368" y1="828" x2="436" y2="828"/>
        <rect x="374" y="810" width="9" height="18"/>
        <rect x="389" y="800" width="9" height="28"/>
        <rect x="404" y="790" width="9" height="38"/>
        <rect x="419" y="772" width="9" height="56"/>
        <polyline points="372,800 392,786 406,790 426,768"/>
      </g>
    </g>
  </g>

  <!-- tagline -->
  <g class="tagline-block">
    <text class="tagline" x="108" y="1451" font-size="35">Be a bright part of our organization.</text>
    <text class="tagline" x="108" y="1495" font-size="35">Become involved and demonstrate</text>
    <text class="tagline" x="108" y="1539" font-size="35">you have the right stuff.</text>
  </g>
</svg>
</div>
</body>
</html>
```